Business card for Eyelash extension salon in Beverly Hills,California USA

We need new business card for our salon in Beverly Hills. The salon name is 'Lashvera' . We would like to have...Business name: Lashvera Name of person: will provide later Address 4720 N.Alder Crest Ave Larkmoor Hills , CA 94017 Phone: will provide later (Text only) Web: www.lashverastudio.example Snapgrid icon, Circlebook icon follow us for seasonal campaign and news @lashverastudiolounge Design should look elegant, high-end, clean, simple, cohesive with my brand. Please refer my brand board. Business name color will be metallic bronzy color. Im thinking grey background or white background. Thanks

Target Market(s)

25-35. Gender neutral. People who are in Entertainment business industry.
This is High-end Eyelash extension salon in Beverly Hills

Industry/Entity Type

Beauty Salon

Contact Information for Business Card

Business name: Lashvera
Name of person: will provide later
Address 4720 N.Alder Crest Ave Larkmoor Hills , CA 94017
Phone: will provide later (Text only)
Web: www.lashverastudio.example
Snapgrid icon, Circlebook icon
follow us for seasonal campaign and news @lashverastudiolounge

Requirements
Must have
• Beautiful, elegant, clean and simple look but very attractive and modern
Should not have
• We don't like too clutter, too busy designs.

```html
<!DOCTYPE html>
<html lang="en">
<head>
<meta charset="utf-8">
<title>Lashvera Business Card</title>
<link rel="stylesheet" href="https://fonts.googleapis.com/css2?family=Open+Sans:wght@300;400;700&display=swap">
<style>
  :root {
    --page-bg: #d9d7d4;
    --card-bg: #121111;
    --bronze: #b08a66;
    --silver: #e4e4e4;
    --text-light: #eeeeee;
    --rule: #4a4847;
  }
  * { box-sizing: border-box; margin: 0; padding: 0; }
  html, body {
    width: 1200px; height: 844px; overflow: hidden;
    background: var(--page-bg);
    font-family: "Open Sans", Arial, sans-serif;
  }
  .stage {
    position: relative; width: 1200px; height: 844px;
    display: flex; align-items: center; justify-content: center; gap: 40px;
  }
  .card {
    position: relative; width: 540px; height: 309px;
    background: var(--card-bg);
    box-shadow: 0 6px 18px rgba(0,0,0,.25);
    overflow: hidden;
  }

  /* Front */
  .front .brand-name {
    position: absolute; left: 40px; top: 128px;
    font-size: 46px; font-weight: 300; color: var(--bronze);
    letter-spacing: 1px;
  }
  .front .divider {
    position: absolute; left: 285px; top: 80px;
    width: 1px; height: 150px; background: var(--rule);
  }
  .front .contact {
    position: absolute; left: 305px; top: 92px;
    color: var(--text-light); font-size: 14px; line-height: 21px;
  }
  .contact .person {
    color: var(--bronze); font-weight: 700; font-size: 16px;
    letter-spacing: .5px; margin-bottom: 6px;
  }
  .contact .line { display: flex; align-items: center; gap: 7px; }
  .contact svg { width: 11px; height: 11px; flex: none; }

  /* Back */
  .back .brand-name {
    position: absolute; left: 0; right: 0; top: 56px; text-align: center;
    font-size: 52px; font-weight: 300; color: var(--silver);
    letter-spacing: 1px;
  }
  .back .rule {
    position: absolute; height: 1px; background: var(--rule);
  }
  .back .rule.top { left: 300px; right: 40px; top: 150px; }
  .back .rule.bottom { left: 40px; right: 40px; top: 228px; }
  .back .social {
    position: absolute; right: 40px; top: 196px;
    display: flex; gap: 6px;
  }
  .social .dot {
    width: 18px; height: 18px; border-radius: 50%; background: var(--text-light);
  }
  .back .follow {
    position: absolute; left: 40px; right: 40px; top: 240px;
    color: var(--text-light); font-size: 14px;
  }
  .follow .handle { font-weight: 700; }
</style>
</head>
<body>
<main class="stage">
  <section class="card front" aria-label="Card front">
    <div class="brand-name">Lashvera</div>
    <div class="divider"></div>
    <div class="contact">
      <div class="person">MARCUS ELLERY</div>
      <div>4720 N.Alder Crest</div>
      <div>Ave Larkmoor Hills , CA 94017</div>
      <div class="line">
        <svg viewBox="0 0 12 12" aria-hidden="true"><path fill="#eeeeee" d="M1 4c0-2 2-3 5-3s5 1 5 3v1H8V4H4v1H1zM2 6h8l1 5H1z"/></svg>
        <span>044-987 654 321</span>
      </div>
      <div class="line">
        <svg viewBox="0 0 12 12" aria-hidden="true"><circle cx="6" cy="6" r="5" fill="none" stroke="#eeeeee" stroke-width="1.4"/><path d="M1 6h10M6 1c-3 3-3 7 0 10M6 1c3 3 3 7 0 10" fill="none" stroke="#eeeeee" stroke-width="1"/></svg>
        <span>www.lashverastudio.example</span>
      </div>
    </div>
  </section>

  <section class="card back" aria-label="Card back">
    <div class="brand-name">Lashvera</div>
    <div class="rule top"></div>
    <div class="social" aria-label="Circlebook and Snapgrid">
      <span class="dot"></span>
      <span class="dot"></span>
    </div>
    <div class="rule bottom"></div>
    <p class="follow">Follow us for seasonal campaign and news <span class="handle">@lashverastudiolounge</span></p>
  </section>
</main>
</body>
</html>
```